Business Card Re-Design/Update

We'd like to update out business cards. I've included our current "Style guide" which has the colour scheme of the organisation in it. I've also included the branding files with logos etc in them.

I've also included a copy of one of our existing cards so that you can see how ugly/dated they look. I'd like a fresh modern corporate look.

Target Market(s)

These are for our clients, potential clients, industry contacts - like all business cards

Contact Information for Business Card

Name
Position
Company Address - Level 1, 47 Fernby Street, Carlow Qld 4072
Direct Phone
mobile
Email
Website -www.korvalit.com.au
Logo

Colors

Designer to choose colors to be used in the design.

Requirements
Must have
• Main Logo
• Cards will need to be editable to be able to personalize them for each new employee.
Nice to have
• The MapOut, ShipWell, KeepSteady would be okay to have if they can be sensibly and professionally added to the look without detracting from the main imagery.
• Maybe they could go on the back of the card? will leave this to your creative discretion as to whether/where they fit.
Should not have
• Should not have decorative or script fonts

```html
<!DOCTYPE html>
<html lang="en">
<head>
<meta charset="utf-8">
<title>korvalIT business card</title>
<link rel="stylesheet" href="https://fonts.googleapis.com/css2?family=Arimo:wght@400;700&family=Questrial&display=swap">
<style>
  :root {
    --page: #e4e4e4;
    --card-light: #ffffff;
    --card-dark: #0c0c0c;
    --brand-red: #d71920;
    --ink: #222222;
    --logo-grey: #333333;
    --logo-grey-dark: #3b3b3b;
    --faint: #ececec;
    --rule: #5a5a5a;
    --ship: #2a8fd8;
    --keep: #c42aa8;
    --map: #6cae3e;
  }
  * { margin: 0; padding: 0; box-sizing: border-box; }
  html, body { width: 1000px; height: 1200px; overflow: hidden; }
  body { background: var(--page); font-family: "Arimo", Arial, sans-serif; position: relative; }

  .card { position: absolute; left: 214px; width: 578px; height: 356px; overflow: hidden; }
  .card-front { top: 219px; background: var(--card-light); border-radius: 0 64px 0 64px; }
  .card-back { top: 607px; background: var(--card-dark); border-radius: 64px 0 64px 0; }

  .backdrop-shape {
    position: absolute; left: -30px; top: 40px; width: 200px; height: 200px;
    background: var(--faint);
  }

  .wordmark { position: absolute; display: flex; align-items: center; gap: 16px; }
  .wordmark-square { width: 46px; height: 46px; background: var(--brand-red); }
  .wordmark-name { font-family: "Questrial", Arial, sans-serif; font-size: 52px; line-height: 1; letter-spacing: -0.5px; }
  .card-front .wordmark { left: 170px; top: 60px; }
  .card-front .wordmark-name { color: var(--logo-grey); }
  .card-back .wordmark { left: 110px; top: 122px; }
  .card-back .wordmark-name { color: var(--logo-grey-dark); }

  .person { position: absolute; left: 49px; top: 182px; }
  .person-name { color: var(--brand-red); font-weight: 700; font-size: 20px; line-height: 24px; }
  .person-role { color: var(--ink); font-size: 16px; line-height: 20px; }

  .contacts { position: absolute; left: 48px; top: 238px; list-style: none; }
  .contacts li { display: flex; align-items: center; gap: 4px; color: var(--ink); font-size: 16px; line-height: 21px; }
  .contacts svg { width: 12px; height: 12px; fill: var(--brand-red); flex: none; }

  .address { position: absolute; right: 35px; top: 282px; text-align: right; color: var(--ink); font-size: 16px; line-height: 21px; font-style: normal; }

  .divider { position: absolute; left: 70px; top: 246px; width: 430px; height: 1px; background: var(--rule); }

  .services { position: absolute; left: 62px; top: 271px; display: flex; gap: 12px; list-style: none; }
  .services li { display: flex; align-items: center; gap: 6px; font-size: 25px; line-height: 30px; }
  .service-square { width: 20px; height: 20px; }
  .service-ship { color: var(--ship); } .service-ship .service-square { background: var(--ship); }
  .service-keep { color: var(--keep); } .service-keep .service-square { background: var(--keep); }
  .service-map { color: var(--map); } .service-map .service-square { background: var(--map); }
</style>
</head>
<body>
  <section class="card card-front" aria-label="Card front">
    <div class="backdrop-shape" aria-hidden="true"></div>
    <div class="wordmark">
      <span class="wordmark-square"></span>
      <span class="wordmark-name">korvalIT</span>
    </div>
    <div class="person">
      <p class="person-name">Daniel Marsh</p>
      <p class="person-role">Position</p>
    </div>
    <ul class="contacts">
      <li><svg viewBox="0 0 12 12" aria-hidden="true"><path d="M3 0h6a1 1 0 0 1 1 1v10a1 1 0 0 1-1 1H3a1 1 0 0 1-1-1V1a1 1 0 0 1 1-1zm0 1.5v8h6v-8z"/></svg>412 730 58214</li>
      <li><svg viewBox="0 0 12 12" aria-hidden="true"><path d="M1 3c2-2 8-2 10 0v2H8.5V3.8h-5V5H1zM2 6h8l1 5H1z"/></svg>412 730 58214</li>
      <li><svg viewBox="0 0 12 12" aria-hidden="true"><path d="M0 2h12v8H0zm1 1v.4l5 3.3 5-3.3V3z"/></svg>info@website.com</li>
      <li><svg viewBox="0 0 12 12" aria-hidden="true"><circle cx="6" cy="6" r="6"/></svg>www.korvalit.com.au</li>
    </ul>
    <address class="address">Level 1, 47 Fernby Street<br>Carlow Qld 4072</address>
  </section>

  <section class="card card-back" aria-label="Card back">
    <div class="wordmark">
      <span class="wordmark-square"></span>
      <span class="wordmark-name">korvalIT</span>
    </div>
    <div class="divider"></div>
    <ul class="services">
      <li class="service-ship"><span class="service-square"></span>ShipWell</li>
      <li class="service-keep"><span class="service-square"></span>KeepSteady</li>
      <li class="service-map"><span class="service-square"></span>MapOut</li>
    </ul>
  </section>
</body>
</html>
```